Simplified minimalist but bold website

Design a website for a brand 'Brighten Every Day' that shares ideas to make managing home and health easier through email swap series, webinars and eventually courses.

Simple landing page to attract users to sign up for a freebie.

Target Market(s)

women with families & homes to run

Number of Pages Required

1 page

Font styles to use
Sans Serif

Colors
e667a6
b768aa
acd136
ffffff
959595

Requirements
Must have
• Simplified look, line icons, opt-in template, contact us form

```html
<!DOCTYPE html>
<html lang="en">
<head>
<meta charset="utf-8">
<title>Brighten Every Day</title>
<link href="https://fonts.googleapis.com/css2?family=Montserrat:wght@300;400;500;600;700&display=swap" rel="stylesheet">
<style>
:root{
  --pink:#e2559e;
  --pink-soft:#ea70ae;
  --blue:#3397cf;
  --blue-soft:#40a5dc;
  --purple:#b054a4;
  --purple-title:#b768aa;
  --green:#9fc929;
  --white:#ffffff;
  --grey:#959595;
  --ink:#3d3d3d;
  --dark:#262626;
}
*{box-sizing:border-box;margin:0;padding:0}
html,body{width:1200px;height:2166px;overflow:hidden}
body{font-family:"Montserrat",sans-serif;color:var(--white);position:relative;background:var(--white)}
.abs{position:absolute}
.center{left:0;width:100%;text-align:center}
p,h1,h2{line-height:1.2}

/* hero */
.hero{top:0;left:0;width:1200px;height:611px;border-top:4px solid var(--blue);
  background:linear-gradient(160deg,#3a3632 0%,#5a5049 40%,#2f2b28 75%,#6d6254 100%)}
.hero-photo{inset:0}
.hero-shade{inset:0;background:rgba(0,0,0,.35)}
.brand{left:115px;top:40px;display:flex;align-items:center;gap:16px}
.brand-dot{width:60px;height:60px;border-radius:50%;background:var(--green)}
.brand-name{font-size:26px;font-weight:400}
.menu-btn{left:1040px;top:49px;width:46px;height:46px;border:2px solid var(--white);border-radius:50%;display:flex;align-items:center;justify-content:center}
.header-rule{left:0;top:140px;width:1200px;height:1px;background:rgba(255,255,255,.2)}
.hero-title{top:242px;font-size:50px;font-weight:400;letter-spacing:1px}
.hero-sub{top:327px;font-size:20px;font-weight:400}
.hero-btn{left:502px;top:388px;width:196px;height:59px;border:2px solid var(--white);border-radius:30px;font-size:17px;font-weight:600;display:flex;align-items:center;justify-content:center;letter-spacing:.5px}
.scroll-down{left:580px;top:524px}

/* offers */
.offer{top:611px;width:600px;height:687px}
.offer-swaps{left:0;background:var(--pink)}
.offer-guide{left:600px;background:var(--blue)}
.eyebrow{top:65px;font-size:13px;font-weight:400}
.offer-title{top:97px;font-size:26px;font-weight:400;letter-spacing:.5px}
.rule{top:144px;left:272px;width:56px;height:4px}
.rule-blue{background:var(--blue)}
.rule-white{background:var(--white)}
.lead{top:179px;font-size:14px;font-weight:700}
.copy{font-size:12px;line-height:16px}
.copy-1{top:213px}.copy-2{top:244px}.copy-3{top:276px}
.pill{top:326px;width:163px;height:47px;border-radius:24px;font-size:12px;font-weight:700;display:flex;align-items:center;justify-content:center}
.pill-blue{left:161px;background:var(--blue)}
.pill-green{left:337px;background:var(--green)}
.ideas{top:411px;font-size:17px;font-weight:600}
.form-box{top:458px;width:394px;height:161px}
.form-pink{left:133px;background:var(--pink-soft)}
.form-blue{left:93px;background:var(--blue-soft)}
.field{left:39px;width:316px;height:30px;background:var(--white);color:#555;font-size:12px;padding-left:26px;display:flex;align-items:center}
.field-1{top:23px}.field-2{top:66px}
.submit{left:39px;top:108px;width:316px;height:31px;font-size:13px;font-weight:700;display:flex;align-items:center;justify-content:center}
.submit-blue{background:var(--blue)}
.submit-purple{background:var(--purple)}
.card{top:195px;width:163px;height:219px;text-align:center}
.card-green{left:113px;background:var(--green)}
.card-purple{left:301px;background:var(--purple)}
.card-icon{position:absolute;left:52px;top:36px}
.card-label{position:absolute;top:111px;width:100%;font-size:18px;font-weight:700}
.card-rule{position:absolute;top:148px;left:67px;width:28px;height:3px}
.card-green .card-rule{background:var(--purple)}
.card-purple .card-rule{background:var(--green)}
.card-text{position:absolute;top:167px;width:100%;font-size:14px;line-height:17px}
.seal{left:562px;top:1275px;width:76px;height:76px;border-radius:50%;background:var(--white);box-shadow:0 0 0 3px rgba(0,0,0,.04)}

/* detail */
.detail{top:1298px;left:0;width:1200px;height:547px;background:linear-gradient(120deg,#f3f3f3 0%,#fbfbfb 45%,#ececec 100%);color:var(--ink)}
.detail-title{top:88px;font-size:32px;font-weight:400;color:var(--purple-title)}
.detail-line{font-size:14.5px}
.detail-btn{left:459px;top:404px;width:282px;height:46px;background:var(--green);color:var(--white);font-size:15px;font-weight:600;display:flex;align-items:center;justify-content:center}

/* footer */
.footer{top:1845px;left:0;width:1200px;height:321px;background:linear-gradient(160deg,#2c2c2c,#1d1d1d 60%,#2a2a2a)}
.social{left:489px;top:72px;display:flex;gap:10px}
.social span{width:48px;height:48px;border:2px solid var(--white);border-radius:50%}
.contact{top:157px;font-size:14px;display:flex;justify-content:center;align-items:center;gap:12px}
.contact svg{vertical-align:-2px;margin-right:6px}
.links{top:196px;font-size:14px;word-spacing:2px}
.legal{top:233px;font-size:14px}
</style>
</head>
<body>

<header class="hero abs">
  <div class="hero-photo abs" role="img" aria-label="Photo of a woman working on a laptop at a wooden table in a clothing studio with dried flowers"></div>
  <div class="hero-shade abs"></div>
  <div class="brand abs"><span class="brand-dot"></span><span class="brand-name">Brighten Every Day</span></div>
  <div class="menu-btn abs">
    <svg width="16" height="14" viewBox="0 0 16 14"><rect y="0" width="16" height="3" fill="#fff"/><rect y="5.5" width="16" height="3" fill="#fff"/><rect y="11" width="16" height="3" fill="#fff"/></svg>
  </div>
  <div class="header-rule abs"></div>
  <h1 class="hero-title abs center">BRIGHTEN EVERY DAY</h1>
  <p class="hero-sub abs center">Chances are life is a little overwhelming</p>
  <div class="hero-btn abs">LET US HELP</div>
  <svg class="scroll-down abs" width="40" height="40" viewBox="0 0 40 40"><circle cx="20" cy="20" r="18" fill="none" stroke="#fff" stroke-width="2"/><path d="M12 14l8 8 8-8M12 21l8 8 8-8" fill="none" stroke="#fff" stroke-width="2"/></svg>
</header>

<section class="offer offer-swaps abs">
  <p class="eyebrow abs center">BABY STEPS… (TRY OUT A FEW OF OUR TRICKS)</p>
  <h2 class="offer-title abs center">SWAPS EMAIL SERIES</h2>
  <div class="rule rule-blue abs"></div>
  <p class="lead abs center">Save TIME, MONEY and SANITY with simple product swaps.</p>
  <p class="copy copy-1 abs center">Reduce the amount of work it takes to run your home.</p>
  <p class="copy copy-2 abs center">Swap out existing products for more sustainable ones.</p>
  <p class="copy copy-3 abs center">Each swap saves you work, clutter, time &amp; money.</p>
  <div class="pill pill-blue abs">SEE SAMPLE SWAP</div>
  <div class="pill pill-green abs">LEARN MORE</div>
  <p class="ideas abs center">Send your ideas my way...</p>
  <form class="form-box form-pink abs">
    <div class="field field-1 abs">NAME</div>
    <div class="field field-2 abs">EMAIL</div>
    <div class="submit submit-blue abs">SEND ME THE GUIDE!</div>
  </form>
</section>

<section class="offer offer-guide abs">
  <p class="eyebrow abs center">BIG LEAP… (I'M READY TO ROLL UP MY SLEEVES)</p>
  <h2 class="offer-title abs center">DECLUTTERING GUIDE</h2>
  <div class="rule rule-white abs"></div>
  <div class="card card-green abs">
    <svg class="card-icon" width="58" height="58" viewBox="0 0 58 58"><circle cx="29" cy="29" r="27" fill="none" stroke="#fff" stroke-width="2"/><rect x="17" y="20" width="24" height="18" fill="none" stroke="#fff" stroke-width="2"/><path d="M17 25h24M21 29h16M21 33h16" stroke="#fff" stroke-width="2"/></svg>
    <div class="card-label">STEPS</div>
    <div class="card-rule"></div>
    <div class="card-text">Let us Help</div>
  </div>
  <div class="card card-purple abs">
    <svg class="card-icon" width="58" height="58" viewBox="0 0 58 58"><circle cx="29" cy="29" r="27" fill="none" stroke="#fff" stroke-width="2"/><path d="M19 27h5v12h-5zM24 28l5-9c2 0 3 2 2 5l-1 3h7c2 0 3 2 2 4l-2 6c-1 2-2 2-3 2H24" fill="none" stroke="#fff" stroke-width="2" stroke-linejoin="round"/></svg>
    <div class="card-label">SIMPLE</div>
    <div class="card-rule"></div>
    <div class="card-text">Chances<br>Let us Help</div>
  </div>
  <form class="form-box form-blue abs">
    <div class="field field-1 abs">NAME</div>
    <div class="field field-2 abs">EMAIL</div>
    <div class="submit submit-purple abs">SIGN ME UP!</div>
  </form>
</section>

<section class="detail abs">
  <div class="abs" style="inset:0" role="img" aria-label="Faint photo of hands using a laptop showing an online shop"></div>
  <h2 class="detail-title abs center">SWAPS EMAIL SERIES</h2>
  <p class="detail-line abs center" style="top:167px">Save TIME, MONEY and SANITY with simple product swaps. And reduce the amount of work it takes to run your</p>
  <p class="detail-line abs center" style="top:209px">home. Swap out existing products for more sustainable ones. Each swap save you work, clutter, time &amp; money.</p>
  <p class="detail-line abs center" style="top:251px">You get an email 2x weekly for 6-12 weeks only Get even more if you feel they are helpful to you</p>
  <p class="detail-line abs center" style="top:293px">Join our monthly SIMPLE SWAP SHARING web jams with other mums and get even more ideas.</p>
  <p class="detail-line abs center" style="top:335px">Better yet, come with great tips of your own to share.</p>
  <div class="detail-btn abs">SIGN ME UP!!</div>
</section>
<div class="seal abs"></div>

<footer class="footer abs">
  <div class="abs" style="inset:0" role="img" aria-label="Dark photo of a laptop keyboard"></div>
  <div class="social abs"><span></span><span></span><span></span><span></span></div>
  <div class="contact abs center">
    <span><svg width="11" height="15" viewBox="0 0 11 15"><path d="M5.5 0A5.5 5.5 0 0 0 0 5.5C0 9.5 5.5 15 5.5 15S11 9.5 11 5.5A5.5 5.5 0 0 0 5.5 0zm0 8a2.5 2.5 0 1 1 0-5 2.5 2.5 0 0 1 0 5z" fill="#fff"/></svg>Sed ut perspiciatis unde omnis..</span>
    <span>|</span>
    <span><svg width="14" height="14" viewBox="0 0 14 14"><path d="M3 0l3 3-2 2c1 2 3 4 5 5l2-2 3 3-2 3C6 14 0 8 0 3z" fill="#fff"/></svg>1 555 010 2020</span>
    <span>|</span>
    <span><svg width="16" height="12" viewBox="0 0 16 12"><rect width="16" height="12" fill="#fff"/><path d="M0 0l8 6 8-6" fill="none" stroke="#262626" stroke-width="1.5"/></svg>hello@brightdayco.com</span>
  </div>
  <p class="links abs center">Help &nbsp; | &nbsp; About &nbsp; | &nbsp; Terms and Conditions &nbsp; | &nbsp; Privacy &nbsp; | &nbsp; FAQ</p>
  <p class="legal abs center">Copyrights © 2018, Brightday Co. All rights reserved.</p>
</footer>

</body>
</html>
```